Coastline Premier Retreats Business Card Design

Design a business card for Coastline Premier Retreats. Look at the website for colors and reference. Card should have logo, name, title, office number, mobile number, email, URL and a tagline like, "Luxury Hotel & Resort Email Marketing" (This might change).

https://www.coastlinepremierretreats.example

The rest I will leave up to your imagination.

Contact Information for Business Card

Logo, name, title, office number, mobile number, email, URL and a tagline like, "Luxury Hotel & Resort Email Marketing" (This might change).

```html
<!DOCTYPE html>
<html lang="en">
<head>
<meta charset="utf-8">
<title>Coastline Premier Retreats – Business Card</title>
<link rel="stylesheet" href="https://fonts.googleapis.com/css2?family=Arimo:wght@400;700&display=swap">
<style>
  :root {
    --stage: #bdbcbd;
    --ink: #0d0d0d;
    --ink-soft: #1c1c1c;
    --paper: #ffffff;
    --accent: #f47a1f;
    --text-grey: #7a7a7a;
    --rule-grey: #b5b5b5;
    --logo-white: #ffffff;
  }
  * { margin: 0; padding: 0; box-sizing: border-box; }
  html, body { width: 1200px; height: 876px; overflow: hidden; }
  body {
    background: var(--stage);
    font-family: "Arimo", Arial, sans-serif;
    position: relative;
  }
  .card {
    position: absolute;
    width: 500px;
    height: 286px;
    overflow: hidden;
    border-radius: 2px;
  }
  .card--front { left: 70px; top: 295px; background: var(--paper); }
  .card--back {
    left: 630px; top: 295px;
    background: radial-gradient(ellipse at 40% 45%, var(--ink-soft), var(--ink) 70%);
  }

  /* front: black header band with orange rule */
  .front-band {
    position: absolute; left: 0; top: 0; width: 100%; height: 108px;
    background: linear-gradient(120deg, var(--ink-soft), var(--ink));
  }
  .front-rule {
    position: absolute; left: 0; top: 108px; width: 100%; height: 3px;
    background: var(--accent);
  }
  .brand {
    position: absolute;
    display: flex; align-items: center; gap: 10px;
    color: var(--logo-white);
    font-weight: 700;
    text-transform: uppercase;
    letter-spacing: 0.06em;
    white-space: nowrap;
  }
  .brand__mark { background: var(--accent); flex: none; }
  .front-band .brand { right: 34px; top: 42px; font-size: 19px; }
  .front-band .brand__mark { width: 14px; height: 14px; }
  .card--back .brand { left: 50%; top: 50%; transform: translate(-50%, -50%); font-size: 25px; }
  .card--back .brand__mark { width: 18px; height: 18px; }

  /* front: identity block */
  .identity {
    position: absolute; left: 26px; top: 140px; width: 188px;
    text-align: right;
  }
  .identity__name {
    color: var(--accent); font-size: 17px; font-weight: 400;
    text-transform: uppercase; letter-spacing: 0.01em;
  }
  .identity__title { color: var(--text-grey); font-size: 12px; margin-top: 4px; }
  .identity__address {
    position: absolute; left: 26px; top: 232px;
    color: var(--text-grey); font-size: 13px; white-space: nowrap;
  }
  .divider {
    position: absolute; left: 232px; top: 138px; width: 1px; height: 80px;
    background: var(--rule-grey);
  }
  .contacts {
    position: absolute; left: 248px; top: 136px;
    list-style: none;
  }
  .contacts li {
    display: flex; align-items: center; gap: 8px;
    color: var(--text-grey); font-size: 13px; line-height: 21px;
    white-space: nowrap;
  }
  .contacts svg { width: 11px; height: 11px; flex: none; fill: none; stroke: var(--accent); stroke-width: 1.6; }
</style>
</head>
<body>

<section class="card card--front" aria-label="Business card front">
  <div class="front-band">
    <div class="brand"><span class="brand__mark"></span>Coastline Premier Retreats</div>
  </div>
  <div class="front-rule"></div>

  <div class="identity">
    <p class="identity__name">Daniel Carter</p>
    <p class="identity__title">Manager</p>
  </div>
  <p class="identity__address">Your Address, City, State, Zip 0000</p>

  <div class="divider"></div>

  <ul class="contacts">
    <li>
      <svg viewBox="0 0 12 12"><path d="M3 1.5 L4.8 3.6 L3.8 5 Q5 7.4 7 8.2 L8.4 7.2 L10.5 9 L9.4 10.6 Q4.6 10.4 1.6 3 Z"/></svg>
      123-456-2100
    </li>
    <li>
      <svg viewBox="0 0 12 12"><rect x="3" y="1" width="6" height="10" rx="1"/><line x1="5.3" y1="9.2" x2="6.7" y2="9.2"/></svg>
      123-456-2100
    </li>
    <li>
      <svg viewBox="0 0 12 12"><rect x="1" y="2.5" width="10" height="7"/><path d="M1 2.5 L6 6.5 L11 2.5"/></svg>
      youremail@mailhost.example
    </li>
    <li>
      <svg viewBox="0 0 12 12"><circle cx="6" cy="6" r="5"/><ellipse cx="6" cy="6" rx="2.2" ry="5"/><line x1="1" y1="6" x2="11" y2="6"/></svg>
      www.coastlinepremierretreats.example
    </li>
  </ul>
</section>

<section class="card card--back" aria-label="Business card back">
  <div class="brand"><span class="brand__mark"></span>Coastline Premier Retreats</div>
</section>

</body>
</html>
```